Business card design for Automotive workshop

We need a business card for a new automotive repair and tyre shop called Keelstone Prime Automotive located in New Zealand. We are a clean, modern and fresh workshop and company.

Front needs to feature logo,
my name:
Marlo Fenwicke (director)

Address:
48 Tarn Lane
Harrowvale 4821

Phone: 07 594 2713
Mobile: 027 451 9362
Email: office@keelstoneautomotive.example.nz
Website: keelstoneautomotive.example.nz

Back needs to feature an area to write down appointment details, date and time.

Also feature a list of jobs and work we do such as,
Vehicle Servicing
All Mechanical Repairs
Warrant of Fitness
Tyres & Wheel Alignments
Automotive Diagnostics
Automotive Parts & Supplies

```html
<!DOCTYPE html>
<html lang="en">
<head>
<meta charset="utf-8">
<title>Keelstone Prime Automotive – Business Card</title>
<link href="https://fonts.googleapis.com/css2?family=Michroma&family=Montserrat:wght@500;600;700&display=swap" rel="stylesheet">
<style>
  :root {
    --stage: #3b3b3d;
    --card-charcoal: #1f1f21;
    --card-black: #141415;
    --brand-red: #e3161f;
    --ink-white: #f4f4f4;
    --rule-grey: #9a9a9a;
    --band-white: #ffffff;
    --dots: #555555;
  }
  * { box-sizing: border-box; margin: 0; padding: 0; }
  html, body {
    width: 1200px; height: 900px; overflow: hidden;
    background: var(--stage);
  }
  .canvas { position: relative; width: 1200px; height: 900px; }
  .card {
    position: absolute; left: 280px; width: 640px; height: 390px;
    overflow: hidden;
    box-shadow: 0 10px 30px rgba(0,0,0,.45);
  }

  /* ---------- Appointment side ---------- */
  .card--appointment { top: 40px; background: var(--card-charcoal); }
  .brand {
    position: absolute; top: 46px; left: 0; right: 0;
    display: flex; justify-content: center; align-items: center; gap: 12px;
  }
  .brand__mark { width: 16px; height: 16px; background: var(--brand-red); }
  .brand__name {
    font-family: "Montserrat", sans-serif; font-weight: 700;
    font-size: 27px; letter-spacing: 2px; text-transform: uppercase;
    color: var(--brand-red);
  }
  .services {
    position: absolute; top: 112px; left: 0; right: 0; text-align: center;
    font-family: "Montserrat", sans-serif; color: var(--ink-white);
  }
  .services__lead {
    font-weight: 700; font-size: 17px; color: var(--brand-red);
    letter-spacing: .5px; margin-bottom: 8px;
  }
  .services__line { font-weight: 500; font-size: 14.5px; line-height: 1.55; }
  .services__dot { color: var(--brand-red); margin: 0 6px; font-weight: 700; }

  .appointment {
    position: absolute; left: 0; right: 0; top: 232px; height: 116px;
    background: var(--band-white);
    padding: 26px 34px 0;
    font-family: "Montserrat", sans-serif;
  }
  .appointment__row { display: flex; align-items: flex-end; gap: 8px; height: 38px; }
  .appointment__label { font-weight: 600; font-size: 15px; color: var(--brand-red); }
  .appointment__line { flex: 1; border-bottom: 2px dotted var(--dots); margin-bottom: 4px; }
  .appointment__line--date { flex: 1.35; }

  /* ---------- Contact side ---------- */
  .card--contact { top: 470px; background: var(--card-black); }
  .texture {
    position: absolute; inset: 0;
    background: radial-gradient(ellipse at 50% 45%, #2c2c2e 0%, #1a1a1b 55%, #0e0e0f 100%);
  }
  .contact {
    position: absolute; top: 108px; left: 0; right: 0; text-align: center;
    font-family: "Michroma", sans-serif; color: var(--ink-white);
  }
  .contact__name {
    font-size: 25px; font-weight: 400; color: var(--brand-red);
    text-transform: uppercase; letter-spacing: .5px;
  }
  .contact__title {
    display: flex; justify-content: center; align-items: center; gap: 8px;
    margin: 4px 0 12px;
    font-size: 13px; text-transform: uppercase; letter-spacing: 1px;
  }
  .contact__rule {
    width: 150px; height: 3px;
    border-top: 1px solid var(--rule-grey); border-bottom: 1px solid var(--rule-grey);
  }
  .contact__line { font-size: 13px; line-height: 1.75; white-space: nowrap; }
  .contact__key { color: var(--brand-red); margin: 0 2px 0 6px; }
  .contact__key:first-child { margin-left: 0; }
</style>
</head>
<body>
<main class="canvas">

  <section class="card card--appointment" aria-label="Appointment side">
    <header class="brand">
      <span class="brand__mark"></span>
      <span class="brand__name">Keelstone Prime Automotive</span>
    </header>

    <div class="services">
      <p class="services__lead">VEHICLE SERVICING</p>
      <p class="services__line">All Mechanical Repairs<span class="services__dot">•</span>Warrant of Fitness<span class="services__dot">•</span>Tyres &amp; Wheel Alignments</p>
      <p class="services__line">Automotive Diagnostics<span class="services__dot">•</span>Automotive Parts &amp; Supplies</p>
    </div>

    <div class="appointment">
      <div class="appointment__row">
        <span class="appointment__label">Date:</span>
        <span class="appointment__line appointment__line--date"></span>
        <span class="appointment__label">Time:</span>
        <span class="appointment__line"></span>
      </div>
      <div class="appointment__row">
        <span class="appointment__label">Date:</span>
        <span class="appointment__line appointment__line--date"></span>
        <span class="appointment__label">Time:</span>
        <span class="appointment__line"></span>
      </div>
    </div>
  </section>

  <section class="card card--contact" aria-label="Contact side">
    <div class="texture" role="img" aria-label="Dark hexagonal mesh grille texture"></div>
    <div class="contact">
      <h1 class="contact__name">Marlo Fenwicke</h1>
      <div class="contact__title">
        <span class="contact__rule"></span>
        <span>Director</span>
        <span class="contact__rule"></span>
      </div>
      <p class="contact__line">48 Tarn Lane, Harrowvale 4821 <span class="contact__key">P.</span>07 594 2713</p>
      <p class="contact__line"><span class="contact__key">C.</span>027 451 9362 <span class="contact__key">E.</span>office@keelstoneautomotive.example.nz</p>
      <p class="contact__line">www.keelstoneautomotive.example.nz</p>
    </div>
  </section>

</main>
</body>
</html>
```